Consulting business card

*1) An Overview:* The business is simply a financial transaction wherein I
offer to provide advice to financial holders of commercial real estate
mortgages (which are sub-performing or non-performing), and said holders
are desirous of selling said mortgages which I will offer advice to said
holders in the purchase of said mortgages. Please note the attached copy
of a proposed line-by-line business card which starts with the 1st line
"RKW Advisory, LLC" with the 2nd line "Purchase of Commercial Mortgage
Loan" and the 3rd line "Sub-performing and Non-performing" is my desired
copy subject to any suggested changes. Please ignore the the copy below
the aforementioned proposed card/copy as it will be activated at a later
date.and advise
*2) The Target Market:* I contact and advise senior officers in banks,
insurance companies, and financial institutions such as CEOs, CFOs, COOs,
and Loan Mitigation Officers: the senior officers are tasked with the
removal of sub-performing and non-performing commercial real estate loans
from their real estate portfolios. The desired market is targeted at $1-10
million USD and located in the US.
*3) Design Specifics: *STYLE should be conservative and be representative
of the financial market contacts; COLOR might show a rich forest green
element, a gold foil accent, and subtle black printing, however,
alternatively, silver foil accent(s) with strong black print would seem in
harmony with the services offered, however, I would appreciate any artful
suggestions; IMAGERY should be subtle (no logo can be strong enough to make
an immediate impact): the quality should make the recipient feel he/she has
just met an experienced and competent financial adviser (I have over 55
years of successful financial and business experience).
720.217.6154davidfredrickjones@gmail.com

```html
<!DOCTYPE html>
<html lang="en">
<head>
<meta charset="utf-8">
<title>RKW Advisory, LLC — Business Card</title>
<link rel="stylesheet" href="https://fonts.googleapis.com/css2?family=Tinos:wght@400;700&family=Arimo:wght@400;700&display=swap">
<style>
  :root {
    --page-bg: #e9e7e2;
    --card-white: #ffffff;
    --gold: #b9a443;
    --gold-light: #c6b45c;
    --gold-text: #a99238;
    --forest: #2d5a2a;
    --ink-light: #ffffff;
  }
  html, body {
    margin: 0;
    padding: 0;
    width: 1200px;
    height: 892px;
    overflow: hidden;
    background: var(--page-bg);
  }
  .business-card {
    position: absolute;
    left: 75px;
    top: 146px;
    width: 1050px;
    height: 600px;
    background: var(--card-white);
    box-shadow: 0 10px 30px rgba(0,0,0,0.18);
    overflow: hidden;
  }
  .card-shapes {
    position: absolute;
    inset: 0;
  }
  .company-name {
    position: absolute;
    left: 420px;
    top: 52px;
    margin: 0;
    font-family: "Tinos", "Times New Roman", serif;
    font-weight: 700;
    font-size: 64px;
    letter-spacing: 1px;
    color: var(--gold-text);
    white-space: nowrap;
  }
  .company-tagline {
    position: absolute;
    left: 398px;
    top: 136px;
    margin: 0;
    font-family: "Arimo", Arial, sans-serif;
    font-weight: 700;
    font-size: 29px;
    line-height: 38px;
    color: var(--forest);
    white-space: nowrap;
  }
  .company-tagline span { display: block; }
  .company-tagline .tagline-second { padding-left: 22px; }
  .person-name {
    position: absolute;
    left: 120px;
    top: 362px;
    margin: 0;
    font-family: "Tinos", "Times New Roman", serif;
    font-weight: 700;
    font-size: 48px;
    color: var(--ink-light);
    white-space: nowrap;
  }
  .contact-divider {
    position: absolute;
    left: 500px;
    top: 424px;
    width: 2px;
    height: 120px;
    background: var(--ink-light);
  }
  .contact-list {
    position: absolute;
    left: 532px;
    top: 434px;
    margin: 0;
    padding: 0;
    list-style: none;
    font-family: "Arimo", Arial, sans-serif;
    font-size: 27px;
    color: var(--ink-light);
  }
  .contact-item {
    display: flex;
    align-items: center;
    gap: 18px;
    height: 50px;
    white-space: nowrap;
  }
  .contact-icon { width: 24px; height: 24px; flex: none; }
</style>
</head>
<body>
  <article class="business-card">
    <svg class="card-shapes" width="1050" height="600" viewBox="0 0 1050 600" aria-hidden="true">
      <defs>
        <linearGradient id="goldFill" x1="0" y1="0" x2="1" y2="1">
          <stop offset="0" style="stop-color:#b6a041"/>
          <stop offset="1" style="stop-color:#c6b45c"/>
        </linearGradient>
      </defs>
      <polygon class="gold-band" points="0,196 118,262 872,438 1050,394 1050,600 0,600" fill="url(#goldFill)"/>
      <polygon class="forest-stripe" points="96,236 900,414 874,428 112,254" fill="#2d5a2a"/>
    </svg>

    <h1 class="company-name">RKW Advisory, LLC</h1>
    <p class="company-tagline">
      <span>Purchase of Commercial Mortgage Loan</span>
      <span class="tagline-second">Sub-performing and Non-performing</span>
    </p>

    <p class="person-name">Marcus Hale</p>
    <div class="contact-divider"></div>
    <ul class="contact-list">
      <li class="contact-item">
        <svg class="contact-icon" viewBox="0 0 24 24" aria-label="Phone">
          <rect x="1" y="3" width="22" height="18" rx="2" fill="#fff"/>
          <path d="M7 8c0 5 4 9 9 9l1.5-2-2.5-1.5-1.2 1c-1.8-.8-3.3-2.3-4.1-4.1l1-1.2L9.2 6.7Z" fill="#b9a443"/>
        </svg>
        <span>555.304.8827</span>
      </li>
      <li class="contact-item">
        <svg class="contact-icon" viewBox="0 0 24 24" aria-label="Email">
          <rect x="1" y="4" width="22" height="16" rx="2" fill="#fff"/>
          <path d="M3 7l9 6 9-6" fill="none" stroke="#b9a443" stroke-width="2"/>
        </svg>
        <span>tomasheraldwick@mailbox.example</span>
      </li>
    </ul>
  </article>
</body>
</html>
```